Calm and Clear Wellness Flyer (new business startup)

One page...clear enough to be read if faxed. This mental health clinic treats depression/anxiety in kids and adults. It also treats opiate and alcohol addiction. It's in downtown Elmira, NY and the owner of the clinic is from Elmira NY, where it's located. This clinic does not take health insurance, so it charges a low rate of $75 a visit once they pay the $125 starting fee.
Updates

Target Market(s)

doctors offices, new patients

Industry/Entity Type

Doctor

Requirements
Must have
• see microsoft word document. pdf is printed on the company letterhead.
Nice to have
• a simplified map would be nice. if you can include the building it would be a plus. The same two fonts were used in the business cards and letter head (kennedy small caps boo*) and Refrigerator Delux.

```html
<!DOCTYPE html>
<html lang="en">
<head>
<meta charset="UTF-8">
<title>Calm and Clear Wellness – Flyer</title>
<link rel="stylesheet" href="https://fonts.googleapis.com/css2?family=Dosis:wght@400;500&family=Lato:ital,wght@0,400;0,700;1,400&display=swap">
<style>
  :root {
    --orange: #e96a30;
    --blue: #29a8df;
    --ink: #3f3f3f;
    --white: #ffffff;
    --page: #f4f4f4;
    --photo-light: #f1f1f1;
    --photo-mid: #c9c9c9;
    --street-light: #f3eeec;
    --street-mid: #dccfca;
    --map-base: #ececec;
    --brick: #7a4a38;
  }
  * { margin: 0; padding: 0; box-sizing: border-box; }
  html, body {
    width: 1200px; height: 1200px; overflow: hidden;
    background: var(--page);
  }
  .flyer {
    position: absolute; left: 237px; top: 88px;
    width: 725px; height: 1024px;
    background: var(--white);
    overflow: hidden;
    font-family: 'Lato', sans-serif;
  }
  .hero-photo {
    position: absolute; left: 0; top: 0; width: 725px; height: 570px;
    background: radial-gradient(ellipse at 62% 30%, var(--photo-light) 0%, #dedede 45%, var(--photo-mid) 100%);
  }
  .street-photo {
    position: absolute; left: 0; top: 570px; width: 725px; height: 392px;
    background: linear-gradient(180deg, var(--street-light) 0%, var(--street-mid) 100%);
  }
  .brand {
    position: absolute; left: 46px; top: 70px;
    display: flex; align-items: center; gap: 18px;
  }
  .brand-dot {
    width: 64px; height: 64px; border-radius: 50%;
    background: var(--orange);
  }
  .brand-name {
    font-family: 'Lato', sans-serif; font-weight: 700;
    font-size: 33px; color: var(--orange); letter-spacing: 0.2px;
    white-space: nowrap;
  }
  .hours {
    position: absolute; left: 0; top: 228px; width: 725px;
    text-align: center; color: var(--orange); font-weight: 700;
  }
  .hours-title { font-size: 34px; line-height: 44px; }
  .hours-days { font-size: 36px; line-height: 46px; }
  .price-card {
    position: absolute; left: 54px; top: 334px; width: 617px; height: 292px;
    background: var(--blue); border-radius: 24px;
    color: var(--white);
    padding: 32px 44px 0 36px;
  }
  .service {
    font-family: 'Dosis', sans-serif; font-weight: 500;
    font-size: 36px; line-height: 44px;
  }
  .price-row { display: flex; align-items: baseline; }
  .leader {
    flex: 1; overflow: hidden; white-space: nowrap;
    letter-spacing: 1px;
  }
  .ages {
    position: absolute; left: 0; bottom: 20px; width: 100%;
    text-align: center; font-size: 28px; letter-spacing: 0.3px;
  }
  .map {
    position: absolute; left: 64px; top: 684px; width: 248px; height: 248px;
    border-radius: 50%; border: 3px solid var(--orange);
    background: radial-gradient(circle at 50% 45%, #f7f7f7 0%, var(--map-base) 70%, #d9e6ef 100%);
  }
  .building {
    position: absolute; left: 20px; top: 761px; width: 116px; height: 73px;
    background: linear-gradient(180deg, #8c5a46 0%, var(--brick) 60%, #4a3a33 100%);
  }
  .conditions {
    position: absolute; left: 350px; top: 648px; width: 360px;
  }
  .conditions-title {
    font-family: 'Dosis', sans-serif; font-weight: 500;
    font-size: 42px; line-height: 44px; color: var(--blue);
  }
  .conditions-list {
    font-family: 'Dosis', sans-serif; font-weight: 400;
    font-size: 35px; line-height: 44px; color: var(--ink);
    margin-top: 4px;
  }
  .motto {
    position: absolute; left: 340px; top: 930px; width: 370px;
    font-family: 'Dosis', sans-serif; font-size: 15px;
    font-style: italic; color: var(--ink); text-align: right;
  }
  .disclaimer {
    position: absolute; left: 0; top: 962px; width: 725px; height: 62px;
    background: var(--orange); color: var(--white);
    font-family: 'Dosis', sans-serif; font-size: 16px; line-height: 20px;
    text-align: center; padding-top: 11px;
  }
</style>
</head>
<body>
  <main class="flyer">
    <div class="hero-photo" role="img" aria-label="Soft grey photo of a phrenology head model"></div>
    <div class="street-photo" role="img" aria-label="Faded photo of the downtown brick clinic building"></div>

    <header class="brand">
      <span class="brand-dot"></span>
      <span class="brand-name">CALM AND CLEAR WELLNESS</span>
    </header>

    <section class="hours">
      <p class="hours-title">HOURS:</p>
      <p class="hours-days">Monday and Saturdays 9-4pm</p>
    </section>

    <section class="price-card">
      <p class="service">Psychiatric Evaluation</p>
      <p class="service price-row"><span>(45min)</span><span class="leader">......................................................................</span><span>$125*</span></p>
      <p class="service">Psychiatric Office Visit</p>
      <p class="service price-row"><span>(15min)</span><span class="leader">......................................................................</span><span>$75*</span></p>
      <p class="ages">AGES:&nbsp; 6 YEARS OLD AND UP</p>
    </section>

    <div class="map" role="img" aria-label="Simplified downtown street map showing the clinic location"></div>
    <div class="building" role="img" aria-label="Photo of the clinic's brick building"></div>

    <section class="conditions">
      <h2 class="conditions-title">Conditions<br>Treated:</h2>
      <p class="conditions-list">Depression, Anxiety,<br>PTSD, ADHD, Addiction,<br>Bipolar, Childhood<br>Mood Disorders</p>
    </section>

    <p class="motto">“We work for you, not the insurance companies”</p>

    <footer class="disclaimer">
      *Although we do not partner with any Health Insurance Companies at this time, a bill will be<br>
      provided to you at the time of service for you to submit to your insurance company.
    </footer>
  </main>
</body>
</html>
```